Open Harbor book needs a cover design

I need a front and back cover design that demonstrates a strong sense of possibility that trust can be repaired even if things look bleak. Repairing trust is difficult, but this book is full of wisdom, proven strategies, and doctoral research to help people strengthen relationships and improve trust. It can help any group: business, nonprofit, education, service. Showing diversity of groups and people is very important. For the cover title, there should be a play on words: "Open Harbor: Is it? Within Reach" should have the words "is it?" crossed out and the words "It IS! should be replaced there in a striking way. Perhaps in red ink. For publishing purposes, book will be titled Open Harbor: It IS Within Reach! Please see the attachment for an example. The book layout is approximately 260 pages.

A business self-help book, but the target is any person in a group that feels they have lost trust in each other. It can be just a normal person struggling in a volunteer group they are a part of, or a supervisor whose group is not working well together. It can be a leader who just wants their group to be stronger.

Business Management

• Allise - I believe is being used on the interior of the book for the title page and headings

• Show hope and possibility in the midst of difficulty. Must have a play on the words in the title "Open Harbor: Is it? Within Reach" with crossing out "is it?" with "It IS!" (see attached example) Must include the author's name: Marla Quentin, PhD Must include a smaller tagline: "Practical Steps to Move Teams Forward Again"
• Showing diverse people, or hands. Diverse kinds of groups - not just business. A colorful cover. Maybe show the complexity of trust when it is broken...broken pieces of trust that are then picked up and put together when people work together. Could show people (or images of hands) or other ways to show that it's a choice and it is possible to repair broken trust. I'd also like to convey a sense of a group - not just random people. That they have something at stake to work on repairing trust together and this book can help them.
• If images of people are used, just showing one gender or race is not okay. Nor just binary choices: like an image containing one man and one woman, or one white person and one person of color - otherwise it seems that the book on Open Harbor is about race or gender relations.

```html
<!DOCTYPE html>
<html lang="en">
<head>
<meta charset="utf-8">
<title>Open Harbor: It IS Within Reach!</title>
<link rel="stylesheet" href="https://fonts.googleapis.com/css2?family=Fresca&family=Gochi+Hand&display=swap">
<style>
  :root {
    --paper: #ffffff;
    --ink: #111111;
    --correction: #8a8a8a;
    --art-peach: #f6c9a8;
    --art-clay: #c8634f;
    --art-cream: #fbe9c6;
  }
  * { margin: 0; padding: 0; box-sizing: border-box; }
  html, body {
    width: 800px;
    height: 1200px;
    overflow: hidden;
    background: var(--paper);
  }
  .cover {
    position: relative;
    width: 800px;
    height: 1200px;
    background: var(--paper);
    color: var(--ink);
    font-family: "Fresca", sans-serif;
    text-align: center;
  }
  .hands-art {
    position: absolute;
    left: 296px;
    top: 12px;
    width: 208px;
    height: 198px;
    border-radius: 40px;
    transform: rotate(45deg) scale(0.78);
    background: linear-gradient(135deg, var(--art-peach) 0%, var(--art-cream) 35%, var(--art-peach) 60%, var(--art-clay) 100%);
  }
  .title {
    position: absolute;
    left: 0;
    width: 100%;
    top: 222px;
    font-weight: 400;
    font-size: 168px;
    line-height: 150px;
    letter-spacing: 2px;
    text-transform: uppercase;
  }
  .title span { display: block; }
  .correction {
    position: absolute;
    left: 236px;
    top: 612px;
    font-family: "Gochi Hand", sans-serif;
    font-size: 84px;
    color: var(--correction);
    transform: rotate(-10deg);
    transform-origin: left bottom;
    letter-spacing: 2px;
  }
  .question {
    position: absolute;
    left: 0;
    width: 100%;
    top: 690px;
    font-size: 86px;
    line-height: 100px;
  }
  .struck {
    position: relative;
    display: inline-block;
  }
  .strike-mark {
    position: absolute;
    left: -4px;
    top: 22px;
    width: calc(100% + 8px);
    height: 66px;
  }
  .strike-mark line {
    stroke: var(--correction);
    stroke-width: 7;
    stroke-linecap: round;
  }
  .subtitle {
    position: absolute;
    left: 0;
    width: 100%;
    top: 790px;
    font-size: 96px;
    line-height: 110px;
  }
  .tagline {
    position: absolute;
    left: 0;
    width: 100%;
    top: 926px;
    font-size: 37px;
    line-height: 40px;
  }
  .author {
    position: absolute;
    left: 0;
    width: 100%;
    top: 1058px;
    font-size: 42px;
  }
</style>
</head>
<body>
<main class="cover">
  <div class="hands-art" role="img" aria-label="Illustration of four hands in different skin tones gripping one another's wrists in a square"></div>

  <h1 class="title"><span>Open</span><span>Harbor</span></h1>

  <p class="correction">It IS</p>

  <p class="question">I<span class="struck">s it<svg class="strike-mark" viewBox="0 0 100 66" preserveAspectRatio="none" aria-hidden="true"><line x1="4" y1="4" x2="96" y2="62"/><line x1="4" y1="62" x2="96" y2="4"/></svg></span>?</p>

  <p class="subtitle">Within Reach!</p>

  <p class="tagline">Practical Steps to Move<br>Teams Forward Again</p>

  <p class="author">Marla Quentin, Ph.D.</p>
</main>
</body>
</html>
```